Resort Room Letter to go in Welcome Basket

It needs the Resort Logo and a snazzier font. Probably some kind of background. It will be in full color. Dimensions 5.5in x 8in. This is the in room letter that goes with the welcome basket.

Text:

Welcome to The Resort! We have prepared this convenient Starter Pack to enhance your stay in our Luxury Condominiums. To further enhance your stay housekeeping will provide daily limited service which includes fresh towels and trash removal. Additional housekeeping services can be scheduled with the front desk for a nominal fee. Please leave the basket so that we can prepare a Starter Pack for the next guest. When you are ready to checkout simply dial **47.

Helpful Hints:

Turn the lever in the freezer to start making ice
The Waterpark can be accessed from the 1st Floor
The Indoor Waterpark is open from 9AM to 11PM
Vending with Snacks & Drinks are available on Floors 1, 2, 4, & 5
The closest grocery store is Brindlemart
You can also conveniently order groceries via Pantrygo from Halvey, Grain Town, & Tressa
Additional convenience items are available for purchase at the Front Desk
Use our Express Checkout by Dialing **47

Thank you so much for choosing the Resort for your Smoky Mountain Vacation!

The Resort Management Team

```html
<!DOCTYPE html>
<html lang="en">
<head>
<meta charset="utf-8">
<title>The Resort – Welcome Letter</title>
<link href="https://fonts.googleapis.com/css2?family=Tinos:ital,wght@0,400;0,700;1,700&display=swap" rel="stylesheet">
<style>
  :root{
    --bg:#d5d5d5;
    --paper:#ffffff;
    --teal:#5a8189;
    --brown:#6a5240;
    --orange:#d99b5a;
    --ink:#222222;
  }
  *{box-sizing:border-box;margin:0;padding:0}
  html,body{width:866px;height:1200px;overflow:hidden;background:var(--bg)}
  body{position:relative;font-family:"Tinos","Times New Roman",serif;color:var(--ink)}

  .letter{position:absolute;left:58px;width:745px;height:510px;background:var(--paper);box-shadow:0 2px 8px rgba(0,0,0,.18)}
  .letter--footer-bar{top:61px}
  .letter--footer-icons{top:636px}

  .band{position:absolute;top:0;height:22px}
  .band--brown{left:58px;width:289px;background:var(--brown)}
  .band--teal{left:347px;width:398px;height:32px;background:var(--teal)}

  .brand{position:absolute;left:0;width:347px;top:80px;text-align:center;font-weight:700;color:var(--brown);line-height:1.05}
  .brand__name{display:block;font-size:40px;letter-spacing:1px}
  .brand__sub{display:block;font-size:18px;margin-top:4px}

  .welcome{position:absolute;left:40px;width:276px;top:205px}
  .welcome__title{text-align:center;color:var(--teal);font-size:16px;font-weight:700;letter-spacing:.6px;margin-bottom:4px}
  .welcome__body{font-size:12px;line-height:20px;text-align:justify}

  .site{position:absolute;left:40px;top:444px;font-size:19.5px;font-weight:700;color:var(--teal);letter-spacing:.2px}

  .hints{position:absolute;left:353px;top:47px;width:378px}
  .hints__title{color:var(--teal);font-size:16px;font-weight:700;letter-spacing:.6px}
  .hints__list{list-style:none}
  .hint{position:absolute;left:0;width:373px;display:flex;align-items:center;transform:translateY(-50%);font-size:12px;line-height:11.5px}
  .hint__tick{flex:0 0 21px;width:21px;height:21px;margin-right:6px}
  .hint__text{text-align:justify;text-align-last:left;flex:1}

  .thanks{position:absolute;left:353px;width:378px;top:384px;text-align:center;font-size:18.5px;font-weight:700;line-height:19.5px;letter-spacing:-.2px}
  .signoff{position:absolute;right:18px;top:450px;font-size:11.5px;font-weight:700;font-style:italic}

  .foot{position:absolute;left:0;width:347px;background:var(--teal);color:#fff}
  .foot--social{top:480px;height:30px;display:flex;align-items:center;justify-content:center;gap:5px;font-size:11.5px}
  .foot--social strong{font-weight:700}
  .foot--site{top:478px;height:32px;display:flex;align-items:center;justify-content:center;font-size:19.5px;font-weight:700}
  .dot{width:16px;height:16px;border-radius:50%;background:#3c5a99;flex:0 0 16px}

  .strip{position:absolute;left:347px;width:329px;background:var(--orange)}
  .strip--review{top:490px;height:20px;display:flex;align-items:center;justify-content:center;gap:6px;font-size:11px;color:#fff}
  .strip--plain{top:488px;height:22px}
  .dot--dark{background:#333;width:13px;height:13px;flex-basis:13px}

  .socials{position:absolute;left:40px;width:290px;top:432px;display:flex;justify-content:space-between;font-size:11px;text-align:center}
  .social{display:flex;flex-direction:column;align-items:center;gap:4px}
  .social .dot{width:20px;height:20px}
</style>
</head>
<body>

<svg width="0" height="0" style="position:absolute">
  <symbol id="tick" viewBox="0 0 21 21">
    <circle cx="10.5" cy="10.5" r="10.5" fill="#d99b5a"/>
    <path d="M5.8 10.8l3.2 3.2 6.4-6.6" fill="none" stroke="#fff" stroke-width="2" stroke-linecap="round" stroke-linejoin="round"/>
  </symbol>
</svg>

<!-- Letter, version with social footer bar -->
<article class="letter letter--footer-bar">
  <div class="band band--brown"></div>
  <div class="band band--teal"></div>

  <div class="brand"><span class="brand__name">The Resort</span><span class="brand__sub">at Warden's Ridge</span></div>

  <section class="welcome">
    <h2 class="welcome__title">Welcome to The Resort!</h2>
    <p class="welcome__body">We have prepared this convenient Starter Pack to enhance your stay in our Luxury Condominiums. To further enhance your stay housekeeping will provide daily limited service which includes fresh towels and trash removal. Additional housekeeping services can be scheduled with the front desk for a nominal fee. Please leave the basket so that we can prepare a Starter Pack for the next guest. When you are ready to checkout simply dial **47 and hang-up.</p>
  </section>

  <div class="site">ResortatWardensRidge.com</div>

  <section class="hints">
    <h2 class="hints__title">Helpful Hints</h2>
    <ul class="hints__list">
      <li class="hint" style="top:37px"><svg class="hint__tick"><use href="#tick"/></svg><span class="hint__text">Turn the lever in the freezer to start making ice</span></li>
      <li class="hint" style="top:67px"><svg class="hint__tick"><use href="#tick"/></svg><span class="hint__text">The Waterpark can be accessed from the 1st Floor</span></li>
      <li class="hint" style="top:96px"><svg class="hint__tick"><use href="#tick"/></svg><span class="hint__text">The Indoor Waterpark is open from 9AM to 11PM</span></li>
      <li class="hint" style="top:126px"><svg class="hint__tick"><use href="#tick"/></svg><span class="hint__text">Vending with Snacks &amp; Drinks are available on Floors 1, 2, 4, &amp; 5</span></li>
      <li class="hint" style="top:155px"><svg class="hint__tick"><use href="#tick"/></svg><span class="hint__text">The closest grocery store is Brindlemart</span></li>
      <li class="hint" style="top:189px"><svg class="hint__tick"><use href="#tick"/></svg><span class="hint__text">You can also conveniently order groceries via Pantrygo from Halvey, Grain Town, &amp; Tressa</span></li>
      <li class="hint" style="top:231px"><svg class="hint__tick"><use href="#tick"/></svg><span class="hint__text">Additional convenience items are available for purchase at the Front Desk</span></li>
      <li class="hint" style="top:266px"><svg class="hint__tick"><use href="#tick"/></svg><span class="hint__text">All deliveries to The Resort must be picked up at the front desk</span></li>
      <li class="hint" style="top:295px"><svg class="hint__tick"><use href="#tick"/></svg><span class="hint__text">Use our Express Checkout by Dialing **47</span></li>
    </ul>
  </section>

  <p class="thanks">Thank you so much for choosing the Resort for your Smoky Mountain Vacation!</p>
  <p class="signoff">The Resort Management Team</p>

  <div class="foot foot--social"><span class="dot"></span>Follow us on Friendloop&nbsp; <strong>TheResortatWardensRidge</strong></div>
  <div class="strip strip--review"><span class="dot dot--dark"></span>Review us on <strong>Tripwise</strong></div>
</article>

<!-- Letter, version with social icons above site bar -->
<article class="letter letter--footer-icons">
  <div class="band band--brown"></div>
  <div class="band band--teal"></div>

  <div class="brand"><span class="brand__name">The Resort</span><span class="brand__sub">at Warden's Ridge</span></div>

  <section class="welcome">
    <h2 class="welcome__title">Welcome to The Resort!</h2>
    <p class="welcome__body">We have prepared this convenient Starter Pack to enhance your stay in our Luxury Condominiums. To further enhance your stay housekeeping will provide daily limited service which includes fresh towels and trash removal. Additional housekeeping services can be scheduled with the front desk for a nominal fee. Please leave the basket so that we can prepare a Starter Pack for the next guest. When you are ready to checkout simply dial **47 and hang-up.</p>
  </section>

  <div class="socials">
    <div class="social"><span class="dot dot--dark"></span>Review us on Tripwise</div>
    <div class="social"><span class="dot"></span>TheResortatWardensRidge</div>
  </div>

  <section class="hints">
    <h2 class="hints__title">Helpful Hints</h2>
    <ul class="hints__list">
      <li class="hint" style="top:37px"><svg class="hint__tick"><use href="#tick"/></svg><span class="hint__text">Turn the lever in the freezer to start making ice</span></li>
      <li class="hint" style="top:67px"><svg class="hint__tick"><use href="#tick"/></svg><span class="hint__text">The Waterpark can be accessed from the 1st Floor</span></li>
      <li class="hint" style="top:96px"><svg class="hint__tick"><use href="#tick"/></svg><span class="hint__text">The Indoor Waterpark is open from 9AM to 11PM</span></li>
      <li class="hint" style="top:126px"><svg class="hint__tick"><use href="#tick"/></svg><span class="hint__text">Vending with Snacks &amp; Drinks are available on Floors 1, 2, 4, &amp; 5</span></li>
      <li class="hint" style="top:155px"><svg class="hint__tick"><use href="#tick"/></svg><span class="hint__text">The closest grocery store is Brindlemart</span></li>
      <li class="hint" style="top:189px"><svg class="hint__tick"><use href="#tick"/></svg><span class="hint__text">You can also conveniently order groceries via Pantrygo from Halvey, Grain Town, &amp; Tressa</span></li>
      <li class="hint" style="top:231px"><svg class="hint__tick"><use href="#tick"/></svg><span class="hint__text">Additional convenience items are available for purchase at the Front Desk</span></li>
      <li class="hint" style="top:266px"><svg class="hint__tick"><use href="#tick"/></svg><span class="hint__text">All deliveries to The Resort must be picked up at the front desk</span></li>
      <li class="hint" style="top:295px"><svg class="hint__tick"><use href="#tick"/></svg><span class="hint__text">Use our Express Checkout by Dialing **47</span></li>
    </ul>
  </section>

  <p class="thanks" style="top:394px">Thank you so much for choosing the Resort for your Smoky Mountain Vacation!</p>
  <p class="signoff" style="right:24px;top:460px">The Resort Management Team</p>

  <div class="foot foot--site">ResortatWardensRidge.com</div>
  <div class="strip strip--plain"></div>
</article>

</body>
</html>
```